HVAC Van wrap design, High end commercial HVAC controls company.

Looking for a clean, professional design that still lists company services.
Some product services include programming HVAC equipment on large buildings, with an eye for energy savings (dont want any cheesy 'green' logo)
Also, Industrial or technical are words I would use to describe the desired look.

Target Market(s)

Commercial HVAC clients, commercial buildings

Industry/Entity Type

Heating, air conditioning and commercial controls (equipment programming)

Requirements
Must have
• 'cool' use of logo

```html
<!DOCTYPE html>
<html lang="en">
<head>
<meta charset="utf-8">
<title>Coreline Mechanical – Van Wrap</title>
<link rel="stylesheet" href="https://fonts.googleapis.com/css2?family=Open+Sans:wght@600;700&family=Raleway:wght@300&display=swap">
<style>
  :root {
    --wrap-white: #f7f7f7;
    --brand-blue: #1aa3d9;
    --accent-cyan: #17bde9;
    --brand-red: #c8101a;
    --text-blue: #1f8ac4;
    --backdrop: #e9ecef;
  }
  html, body {
    margin: 0;
    padding: 0;
    width: 1200px;
    height: 573px;
    overflow: hidden;
    background: var(--backdrop);
  }
  .wrap-panel {
    display: block;
    width: 1200px;
    height: 573px;
  }
  .panel-base { fill: var(--wrap-white); }
  .swoosh { fill: var(--accent-cyan); }
  .rule { stroke: var(--brand-red); stroke-width: 1.6; }
  .website {
    font-family: "Open Sans", sans-serif;
    font-weight: 700;
    font-size: 22px;
    letter-spacing: 1.5px;
    fill: var(--brand-red);
  }
  .phone {
    font-family: "Open Sans", sans-serif;
    font-weight: 600;
    font-size: 21px;
    fill: var(--text-blue);
  }
  .phone-badge { fill: var(--brand-red); }
  .phone-icon { fill: #fff; }
  .brand-name {
    font-family: "Raleway", sans-serif;
    font-weight: 300;
    fill: var(--brand-blue);
  }
  .brand-primary { font-size: 96px; letter-spacing: 2px; }
  .brand-secondary { font-size: 58px; letter-spacing: 3px; }
  .services {
    font-family: "Open Sans", sans-serif;
    font-weight: 700;
    font-size: 14.5px;
    letter-spacing: 1.2px;
    fill: var(--text-blue);
  }
  .bullet { fill: var(--brand-red); }
</style>
</head>
<body>
<svg class="wrap-panel" viewBox="0 0 1200 573" xmlns="http://www.w3.org/2000/svg">
  <defs>
    <clipPath id="panel-clip">
      <rect x="0" y="0" width="1200" height="573"/>
    </clipPath>
  </defs>

  <g clip-path="url(#panel-clip)">
    <rect class="panel-base" x="0" y="0" width="1200" height="573"/>

    <!-- accent shapes -->
    <circle class="swoosh" cx="494" cy="70" r="118"/>
    <circle class="swoosh" cx="985" cy="410" r="135"/>

    <!-- divider rules -->
    <line class="rule" x1="347" y1="398" x2="461" y2="366"/>
    <line class="rule" x1="869" y1="254" x2="983" y2="221"/>

    <!-- web address -->
    <text class="website" transform="translate(468 229) rotate(-16.5)">WWW.CORELINEMECHANICAL.COM</text>

    <!-- phone -->
    <g class="phone-line" transform="translate(220 296) rotate(-16.5)">
      <circle class="phone-badge" cx="0" cy="0" r="13"/>
      <path class="phone-icon" d="M-5.5 -6 l3 -1.2 l2.2 4 l-2 1.4 q1.2 3 4.2 4.4 l1.4 -2 l4 2.2 l-1.2 3 q-1 1.2 -3 0.6 q-7 -2.8 -9.4 -9.6 q-0.6 -2 0.8 -2.8z"/>
      <text class="phone" x="20" y="8">+1 800-555-0142</text>
    </g>

    <!-- company name -->
    <text class="brand-name brand-primary" transform="translate(320 362) rotate(-19)">CORELINE</text>
    <text class="brand-name brand-secondary" transform="translate(503 370) rotate(-18)">MECHANICAL</text>

    <!-- services -->
    <text class="services" transform="translate(450 410) rotate(-16.5)"><tspan class="bullet">•</tspan> CONTROLS/ PROGRAMMING <tspan class="bullet">•</tspan>COMMERCIAL CLIMATE MASTERY</text>
    <text class="services" transform="translate(596 396) rotate(-16.5)"><tspan class="bullet">•</tspan>RESIDENTIAL SOLUTIONS</text>
  </g>
</svg>
</body>
</html>
```